A private security company called "Tavron Security Services Ltd"

Hello everybody,

We need a web page for a company based in NZ. It is mainly an informative website so it would be wonderful if the designer puts their absolute best into making it a website that I would really appreciate. The website needs to show professionalism and also needs to make our web surfers find the information they need in a click. the company's colour is black and silver, and if those two colours could be integrated into the website it would be absolutely lovely. Please do contact me for any information.

Sincerely,
Dorian Vaskel

Industry/Entity Type

Security

```html
<!DOCTYPE html>
<html lang="en">
<head>
<meta charset="utf-8">
<title>Tavron Security Services Ltd</title>
<link href="https://fonts.googleapis.com/css2?family=Josefin+Sans:wght@400;600&family=Open+Sans:ital,wght@0,400;0,600;0,700;1,400&display=swap" rel="stylesheet">
<style>
:root{
  --green:#8fb33a;
  --green-light:#b5d567;
  --green-dark:#6f9426;
  --ink:#1c1c1c;
  --nav:#2b2b2b;
  --panel:#303030;
  --text:#555;
  --grey-bar:#ececec;
  --line:#9a9a9a;
  --footer:#000;
  --white:#fff;
}
*{margin:0;padding:0;box-sizing:border-box}
html,body{width:915px;height:1200px;overflow:hidden;background:var(--white)}
body{position:relative;font-family:"Open Sans",Arial,sans-serif;color:var(--text)}
.abs{position:absolute}
a{color:inherit;text-decoration:none}

/* utility bar */
.util-bar{left:0;top:0;width:915px;height:24px;background:var(--grey-bar)}
.util-link{top:6px;font-size:8.6px;line-height:11px;color:#222;white-space:nowrap}
.util-sep{top:6px;font-size:8.6px;line-height:11px;color:#666}
.lang{left:734px;top:5px;font-size:9px;line-height:12px;color:#555;display:flex;align-items:center;gap:6px;white-space:nowrap}
.lang b{font-weight:400;color:#222}
.flag{width:17px;height:11px;background:linear-gradient(#b22 0 50%,#fff 50% 100%);background-size:100% 2.2px;position:relative;flex:none}
.flag::before{content:"";position:absolute;left:0;top:0;width:8px;height:6px;background:#2c3e86}

/* header */
.call{left:640px;top:40px;display:flex;align-items:center;gap:7px;font-size:14.5px;color:var(--ink)}
.call b{font-weight:400;color:var(--green-dark)}
.navbar{left:0;top:83px;width:915px;height:41px;background:linear-gradient(#3a3a3a,#222)}
.brand-tab{left:0;top:83px}
.brand{left:136px;top:52px;width:160px;text-align:center;font-family:"Josefin Sans",sans-serif;font-weight:600;color:var(--ink)}
.brand .mark{display:block;width:14px;height:14px;background:var(--ink);margin:0 auto 6px}
.brand .name{font-size:18px;letter-spacing:1px;line-height:1}
.brand .sub{font-size:9.5px;letter-spacing:.3px;margin-top:3px}
.nav{left:334px;top:83px;height:41px;display:flex;align-items:center;font-size:9.6px;color:var(--white);font-weight:600}
.nav a{padding:0 18px;white-space:nowrap}
.nav .slash{color:#777;font-size:16px;font-weight:300}

/* hero */
.hero-bg{left:0;top:124px}
.hero-photo{left:560px;top:124px;width:253px;height:286px;background:radial-gradient(ellipse at 60% 40%,#c7ccd2 0%,#8e959d 45%,#dfe6ee 80%,#eef3f8 100%)}
.hero-title{left:149px;top:190px;font-family:"Josefin Sans",sans-serif;font-size:29px;line-height:31px;color:var(--ink);font-weight:400}
.hero-copy{left:151px;top:253px;width:325px;font-size:10px;line-height:14.6px;color:#444}
.btn{left:150px;top:325px;width:82px;height:23px;background:#333;color:var(--white);font-size:9.5px;font-weight:600;border-radius:2px;display:flex;align-items:center;justify-content:center}
.dots{left:429px;top:426px;display:flex;gap:6px}
.dots i{width:10px;height:10px;border-radius:50%;background:#222}
.dots i.on{background:#d8d8d8}

/* service cards */
.card{top:482px;width:151px;height:258px;background:var(--white);border:1px solid #ddd;box-shadow:0 1px 3px rgba(0,0,0,.18)}
.card .thumb{height:88px}
.card h3{margin:19px 0 0 10px;font-family:"Josefin Sans",sans-serif;font-weight:400;font-size:17px;line-height:22px;color:var(--ink)}
.card p{margin:10px 12px 0 11px;font-size:10px;line-height:19px;color:#666}
.card .more{display:inline-block;margin:7px 0 0 12px;font-style:italic;font-size:10.5px;color:var(--green-dark);border-bottom:1px solid var(--green)}

/* intro & video */
.sec-head{font-family:"Josefin Sans",sans-serif;font-size:17.5px;font-weight:400;color:var(--ink);border-bottom:1px solid var(--line);padding-bottom:5px;white-space:nowrap}
.sec-head b{font-weight:600}
.intro-head{left:126px;top:772px;width:409px}
.intro-copy{left:127px;top:812px;width:410px;font-size:10px;line-height:21.5px;color:#555}
.intro-more{left:126px;top:928px;font-size:11px;color:var(--ink);display:flex;align-items:center;gap:7px}
.video-head{left:569px;top:772px;width:219px}
.video{left:571px;top:816px;width:217px;height:125px;background:linear-gradient(#cfd1d3,#e6e7e8 60%,#bfc1c3)}
.video-bar{left:571px;top:926px;width:217px;height:15px;background:#1b1b1b}
.video-progress{left:571px;top:926px;width:62px;height:2px;background:#d12}

/* footer */
.footer{left:0;top:973px;width:915px;height:182px;background:var(--footer)}
.fcol{top:992px;color:var(--white)}
.fcol h4{font-size:11.5px;font-weight:600;margin-bottom:13px}
.fcol li{list-style:none;font-size:9.3px;line-height:17.6px;color:#ddd}
.social{left:612px;top:1028px;display:flex;gap:4px}
.social i{width:24px;height:24px;background:#555}
.f-phone{left:611px;top:1063px;font-size:17.5px;font-weight:700;color:var(--white);letter-spacing:.3px}
.search{left:612px;top:1098px;width:178px;height:23px;background:var(--white);border-radius:2px;font-size:9px;color:#999;padding:5px 9px}
.search svg{position:absolute;right:7px;top:5px}
.copyright{left:0;top:1170px;width:915px;text-align:center;font-size:9.5px;color:#333}
</style>
</head>
<body>

<div class="abs util-bar"></div>
<a class="abs util-link" style="left:518px">Customer Service</a>
<span class="abs util-sep" style="left:598px">|</span>
<a class="abs util-link" style="left:612px">About Us</a>
<span class="abs util-sep" style="left:660px">|</span>
<a class="abs util-link" style="left:675px">Contact Us</a>
<div class="abs lang"><span class="flag"></span><span>(EN) <b>English</b> ▾</span></div>

<div class="abs call">
  <svg width="24" height="24" viewBox="0 0 24 24"><circle cx="12" cy="12" r="10.5" fill="none" stroke="#8fb33a" stroke-width="1.8"/><path d="M8.5 7c.8-.6 1.5-.4 2 .5l.6 1.3c.3.7 0 1.1-.5 1.5-.4.3-.3.7 0 1.3.6 1 1.300 1.8 2.2 2.4.5.3.9.3 1.2-.1.5-.6 1-.8 1.6-.4l1.2.8c.8.6.8 1.3.1 2-1.4 1.3-3.4.8-5.3-.8-1.7-1.4-3-3.3-3.4-5-.3-1.3 0-2.2.3-2.5z" fill="#8fb33a"/></svg>
  <span>CALL : <b>555-214-3860</b></span>
</div>

<div class="abs navbar"></div>
<svg class="abs brand-tab" width="915" height="36" viewBox="0 0 915 36"><polygon points="116,0 300,0 285,35 128,35" fill="#fff"/><polygon points="0,0 116,0 117,2 0,2" fill="#fff"/></svg>
<div class="abs brand">
  <span class="mark"></span>
  <div class="name">TAVRON</div>
  <div class="sub">Security Services Ltd.</div>
</div>
<nav class="abs nav">
  <a>HOME</a><span class="slash">/</span><a>WHO WE ARE</a><span class="slash">/</span><a>SOLUTIONS</a><span class="slash">/</span><a>CUSTOMER SUPPORT</a><span class="slash">/</span><a>SERVICES</a>
</nav>

<svg class="abs hero-bg" width="915" height="390" viewBox="0 0 915 390">
  <defs>
    <linearGradient id="sideGreen" x1="0" y1="0" x2="1" y2="0">
      <stop offset="0" stop-color="#8fb33a"/><stop offset=".5" stop-color="#b5d567"/><stop offset="1" stop-color="#8fb33a"/>
    </linearGradient>
    <linearGradient id="slideWhite" x1="0" y1="0" x2="1" y2="0">
      <stop offset="0" stop-color="#eef2f6"/><stop offset=".5" stop-color="#fff"/><stop offset="1" stop-color="#e9eef3"/>
    </linearGradient>
  </defs>
  <polygon points="0,0 915,0 915,272 0,272" fill="url(#sideGreen)"/>
  <polygon points="0,0 60,0 105,140 105,272 0,260" fill="#a6c94f" opacity=".6"/>
  <polygon points="915,0 855,0 813,140 813,272 915,260" fill="#a6c94f" opacity=".6"/>
  <polygon points="105,280 813,280 813,386 105,386" fill="#303030"/>
  <polygon points="105,0 813,0 813,272 457,306 105,272" fill="url(#slideWhite)"/>
  <polygon points="105,272 457,306 813,272 813,282 457,328 105,282" fill="#8fb33a"/>
  <polygon points="0,272 105,272 105,282 0,272" fill="#8fb33a"/>
  <polygon points="915,272 813,272 813,282 915,272" fill="#8fb33a"/>
</svg>
<div class="abs hero-photo" role="img" aria-label="Close-up photo of an outdoor CCTV security camera"></div>
<h1 class="abs hero-title">WELCOME TO TAVRON<br>SECURITY SERVICES</h1>
<p class="abs hero-copy">Lorem Ipsum is simply dummy text of the printing and typesetting industry. Lorem Ipsum has been the industry's standard dummy text ever since the 1500s, when an unknown printer took a galley of type and scrambled it to make a type specimen book. unchanged.</p>
<a class="abs btn">READ MORE</a>
<div class="abs dots"><i></i><i class="on"></i><i></i><i></i></div>

<div class="abs card" style="left:124px">
  <div class="thumb" role="img" aria-label="Photo of a uniformed guard with a duty belt" style="background:linear-gradient(90deg,#c9d3dc,#8795a6 60%,#2a3550)"></div>
  <h3>PROPERTY<br>SECURITY</h3>
  <p>Lorem Ipsum is simply dummy text of the printing and typesetting industry.</p>
  <a class="more">Learn More</a>
</div>
<div class="abs card" style="left:295px">
  <div class="thumb" role="img" aria-label="Photo of two businessmen shaking hands" style="background:linear-gradient(120deg,#8a8f93,#2b2d30 55%,#6e7378)"></div>
  <h3>SECURITY<br>CONSULTANCY</h3>
  <p>Lorem Ipsum is simply dummy text of the printing and typesetting industry.</p>
  <a class="more">Learn More</a>
</div>
<div class="abs card" style="left:466px">
  <div class="thumb" role="img" aria-label="Photo of an event security officer facing a crowd" style="background:linear-gradient(90deg,#9c8f84,#1e1f22 45%,#8da06a)"></div>
  <h3>EVENTS<br>SECURITY</h3>
  <p>Lorem Ipsum is simply dummy text of the printing and typesetting industry.</p>
  <a class="more">Learn More</a>
</div>
<div class="abs card" style="left:637px">
  <div class="thumb" role="img" aria-label="Photo of bodyguards escorting a black car" style="background:linear-gradient(#a8adb2,#3a3c40 60%,#7d8186)"></div>
  <h3>PERSONAL<br>BODYGUARDS</h3>
  <p>Lorem Ipsum is simply dummy text of the printing and typesetting industry.</p>
  <a class="more">Learn More</a>
</div>

<h2 class="abs sec-head intro-head">Welcome to <b>Tavron Security Services</b></h2>
<p class="abs intro-copy">Lorem Ipsum is simply dummy text of the printing and typesetting industry. Lorem Ipsum has been the industry's standard dummy text ever since the 1500s, when an unknown printer took a galley of type and scrambled it to make a type specimen book. It has survived not only five centuries, but also the leap into electronic typeset­ting, remaining essentially unchanged. It was popularised in the 1960s with the</p>
<a class="abs intro-more">Learn More <svg width="6" height="7" viewBox="0 0 6 7"><polygon points="0,0 6,3.5 0,7" fill="#3b3bb0"/></svg></a>

<h2 class="abs sec-head video-head">Our <b>Video</b></h2>
<div class="abs video" role="img" aria-label="Video still of a dome security camera on a ceiling"></div>
<div class="abs video-bar"></div>
<div class="abs video-progress"></div>

<footer class="abs footer"></footer>
<div class="abs fcol" style="left:131px"><h4>Services</h4><ul><li>Property Guards</li><li>Event Security</li><li>Personal Bodyguard</li><li>Security Consultancy</li><li>Private Investigation</li></ul></div>
<div class="abs fcol" style="left:291px"><h4>Technical Center</h4><ul><li>Installation</li><li>Drawings</li><li>Faqs</li><li>Documents</li></ul></div>
<div class="abs fcol" style="left:454px"><h4>About Us</h4><ul><li>Sustainability</li><li>News</li><li>Careers</li><li>Testimonials</li><li>Warranty</li><li>Registration</li></ul></div>
<div class="abs fcol" style="left:611px"><h4>Contact Us</h4></div>
<div class="abs social" aria-label="Social links"><i></i><i></i><i></i><i></i></div>
<div class="abs f-phone">555-214-3860</div>
<div class="abs search">Search
  <svg width="12" height="12" viewBox="0 0 12 12"><circle cx="5" cy="5" r="3.8" fill="none" stroke="#444" stroke-width="1.4"/><line x1="7.8" y1="7.8" x2="11" y2="11" stroke="#444" stroke-width="1.6"/></svg>
</div>

<div class="abs copyright">©2014 Tavron Security Services. All Rights Reserved</div>

</body>
</html>
```